VelkaVision.com

Complete Website Design (Godaddy) and company Branding / Logo Design. The products will sell are only done in-person and are installed. So this site does not need to be an e-commerce site. We will only be giving out information and collecting customer inquires. Website will only need to be about 3 to 5 pages.

```html
<!DOCTYPE html>
<html lang="en">
<head>
<meta charset="utf-8">
<title>VelkaVision – Professional Projector Installation</title>
<link href="https://fonts.googleapis.com/css2?family=Ubuntu:wght@500;700&family=Lato:wght@400;700&display=swap" rel="stylesheet">
<style>
:root{
  --blue:#2353cc;
  --navy:#263257;
  --ink:#222427;
  --footer:#282828;
  --frame:#2e5a8a;
  --white:#ffffff;
  --placeholder:#7b7f86;
}
*{box-sizing:border-box;margin:0;padding:0}
html,body{width:1057px;height:1200px;overflow:hidden;background:var(--white)}
body{position:relative;font-family:'Lato',sans-serif}
.hero{position:absolute;left:0;top:0;width:1057px;height:453px;
  background:linear-gradient(100deg,#5e8a80 0%,#8fa6b0 22%,#cfd8de 45%,#eef1f3 62%,#f4f5f6 100%)}
.hero-photo{position:absolute;left:0;top:0;width:600px;height:453px;
  background:radial-gradient(ellipse at 45% 55%,rgba(40,90,100,.55),rgba(200,210,215,0) 70%)}
.contact-btn{position:absolute;left:98px;top:32px;width:117px;height:41px;background:var(--blue);
  color:var(--white);font-family:'Ubuntu',sans-serif;font-weight:500;font-size:14px;
  display:flex;align-items:center;justify-content:center;border-radius:10px 0 10px 0;text-decoration:none}
.logo{font-family:'Ubuntu',sans-serif;font-weight:700;color:var(--blue);letter-spacing:.5px}
.header-logo{position:absolute;left:0;width:1057px;top:24px;text-align:center;font-size:40px}
.menu{position:absolute;left:935px;top:42px}
.hero-title{position:absolute;left:568px;width:400px;top:192px;text-align:center;
  font-family:'Ubuntu',sans-serif;font-weight:700;font-size:31px;line-height:41px;color:var(--ink)}
.hero-title .accent{color:var(--blue);display:block}
.frame{position:absolute;left:72px;top:541px;width:917px;height:371px;border:2px solid var(--frame)}
.consult{position:absolute;left:65px;top:537px;width:918px;height:369px;
  background:linear-gradient(115deg,var(--navy) 0%,#243f8c 40%,#1f52c8 75%,#2152cc 100%)}
.consult h2{position:absolute;top:36px;width:100%;text-align:center;font-family:'Ubuntu',sans-serif;
  font-weight:500;font-size:33px;color:var(--white)}
.field{position:absolute;background:var(--white);height:45px;width:272px;
  font-size:13.5px;color:var(--placeholder);padding:14px 21px}
.message{height:73px;width:834px}
.submit{position:absolute;left:389px;top:303px;width:151px;height:41px;background:var(--ink);
  color:var(--white);font-weight:700;font-size:13px;display:flex;align-items:center;justify-content:center}
.site-footer{position:absolute;left:0;top:983px;width:1057px;height:217px;background:var(--footer);text-align:center}
.footer-logo{position:absolute;width:100%;top:49px;font-size:40px}
.social{position:absolute;left:483px;top:110px;display:flex;gap:4px}
.social span{width:28px;height:28px;border:1.5px solid var(--white);border-radius:50%}
.copyright{position:absolute;width:100%;top:153px;color:var(--white);font-size:14px}
</style>
</head>
<body>
<header class="hero" role="img" aria-label="Technician in a cap and plaid shirt mounting a ceiling projector in a bright room">
  <div class="hero-photo"></div>
</header>
<a class="contact-btn" href="#">Contact Us</a>
<div class="logo header-logo">VelkaVision</div>
<svg class="menu" width="24" height="20" viewBox="0 0 24 20" aria-label="Menu">
  <rect y="0" width="24" height="3" fill="#222427"/><rect y="8.5" width="24" height="3" fill="#222427"/><rect y="17" width="24" height="3" fill="#222427"/>
</svg>
<h1 class="hero-title">PROFESSIONAL<br>PROJECTOR<span class="accent">INSTALLATION SERVICES</span></h1>

<div class="frame"></div>
<section class="consult">
  <h2>SCHEDULE A CONSULTATION</h2>
  <div class="field" style="left:47px;top:100px">First Name*</div>
  <div class="field" style="left:328px;top:100px">Last Name*</div>
  <div class="field" style="left:609px;top:100px">Email*</div>
  <div class="field" style="left:47px;top:153px">Phone</div>
  <div class="field" style="left:328px;top:153px">Address</div>
  <div class="field" style="left:609px;top:153px">City or Town</div>
  <div class="field message" style="left:47px;top:208px">How Can We Assist You</div>
  <div class="submit">SUBMIT</div>
</section>

<footer class="site-footer">
  <div class="logo footer-logo">VelkaVision</div>
  <div class="social" aria-label="Social links"><span></span><span></span><span></span></div>
  <p class="copyright">2024 Velka Vision. All Rights Reserved.</p>
</footer>
</body>
</html>
```